Baby Organic Coconut Body Lotion

Meadow Hush Naturals is developing a line of Organic and Natural skin care products for babies and toddlers, although our skin care can also be used by adults too. These products include a body lotion, shampoo & body wash, powder, hair cream, massage body oil, bath soak, baby balm, Bar Soap, gift box and many more.
This will be an ever expanding line so the list will go on and on. We are looking forward for an eye catching designs. I attached some of our current label designs and product images. Also, we have different Baby organic body lotion and Baby organic shampoo & body wash with different fruit flavours. Coconut lotion will share the same design with the shampoo & body wash. I would like you to start with the coconut design. I have uploaded plastic bottles with different colourful caps. The bottle with the white cap is for the coconut design. the bottle with the red cap is for the strawberry design. the bottle with the orange cap is for the orange design. the bottle with the yellow cap is for the pineapple design. the bottle with the green cap is for the apple design. Bear in my mind that my baby organic skin care are made with different fruit flavours.
Target Market(s)
My target market are for mothers that wants to buy there baby and toddler skin care products.
Industry/Entity Type
Baby
Look and feel

```html
<!DOCTYPE html>
<html lang="en">
<head>
<meta charset="utf-8">
<title>Meadow Hush Naturals – Strawberry Labels</title>
<link rel="stylesheet" href="https://fonts.googleapis.com/css2?family=Antonio:wght@100&family=Josefin+Sans:wght@300&family=Montserrat:wght@800&display=swap">
<style>
  :root {
    --ink: #000000;
    --berry: #ef5350;
    --paper: #ffffff;
    --brand-font: "Antonio", sans-serif;
    --flavour-font: "Montserrat", sans-serif;
    --detail-font: "Josefin Sans", sans-serif;
  }
  * { margin: 0; padding: 0; box-sizing: border-box; }
  html, body { width: 1200px; height: 1000px; overflow: hidden; background: var(--paper); }
  .canvas { position: relative; width: 1200px; height: 1000px; background: var(--paper); }
  .label { position: absolute; top: 0; width: 374px; height: 1000px; color: var(--ink); }
  .label--lotion { left: 150px; }
  .label--wash { left: 651px; }
  .label__art { position: absolute; inset: 0; width: 374px; height: 1000px; }
  .brand { position: absolute; left: 0; width: 374px; text-align: center; font-family: var(--brand-font); font-weight: 100; color: var(--ink); }
  .brand__line { position: absolute; left: 0; width: 100%; line-height: 1; }
  .brand__line--top { top: 112px; font-size: 104px; letter-spacing: 4px; }
  .brand__line--mid { top: 228px; font-size: 46px; letter-spacing: 2px; }
  .brand__line--bottom { top: 262px; font-size: 104px; letter-spacing: 2px; }
  .flavour { position: absolute; left: 0; width: 374px; top: 656px; line-height: 48px; text-align: center; font-family: var(--flavour-font); font-weight: 800; font-size: 41px; letter-spacing: -1px; }
  .product { position: absolute; left: 0; width: 374px; text-align: center; font-family: var(--detail-font); font-weight: 300; font-size: 27px; letter-spacing: 3px; line-height: 32px; top: 729px; }
  .product--wide { letter-spacing: 2px; font-size: 26px; }
  .size-mark { position: absolute; left: 0; width: 374px; top: 796px; line-height: 44px; text-align: center; font-family: var(--detail-font); font-weight: 300; font-size: 44px; }
</style>
</head>
<body>
<main class="canvas">
  <section class="label label--lotion">
    <svg class="label__art" viewBox="0 0 374 1000" aria-hidden="false">
      <polygon class="badge-frame" points="187,478 362,577 362,778 187,878 13,778 13,577" fill="var(--berry)" stroke="var(--ink)" stroke-width="8" stroke-linejoin="miter"/>
      <polygon class="badge-panel" points="187,500 344,589 344,767 187,857 30,767 30,589" fill="var(--paper)"/>
      <ellipse class="fruit-art" cx="222" cy="515" rx="84" ry="100" fill="var(--berry)" stroke="var(--ink)" stroke-width="6" role="img" aria-label="Strawberry illustration with green leaves"/>
      <polygon class="star" points="88,582 93,594 106,594 96,602 100,615 88,607 76,615 80,602 70,594 83,594" fill="var(--ink)"/>
      <polygon class="star" points="290,582 295,594 308,594 298,602 302,615 290,607 278,615 282,602 272,594 285,594" fill="var(--ink)"/>
      <g class="rules" stroke="var(--ink)" stroke-width="3">
        <line x1="122" y1="627" x2="252" y2="627"/>
        <line x1="43" y1="640" x2="331" y2="640"/>
        <line x1="43" y1="708" x2="331" y2="708"/>
        <line x1="122" y1="721" x2="252" y2="721"/>
      </g>
    </svg>
    <h1 class="brand">
      <span class="brand__line brand__line--top">MEADOW</span>
      <span class="brand__line brand__line--mid">HUSH</span>
      <span class="brand__line brand__line--bottom">NATURALS</span>
    </h1>
    <p class="flavour">STRAWBERRY</p>
    <p class="product">BODY<br>LOTION</p>
    <p class="size-mark">T</p>
  </section>

  <section class="label label--wash">
    <svg class="label__art" viewBox="0 0 374 1000" aria-hidden="false">
      <polygon class="badge-frame" points="187,478 362,577 362,778 187,878 13,778 13,577" fill="var(--berry)" stroke="var(--ink)" stroke-width="8" stroke-linejoin="miter"/>
      <polygon class="badge-panel" points="187,500 344,589 344,767 187,857 30,767 30,589" fill="var(--paper)"/>
      <ellipse class="fruit-art" cx="222" cy="515" rx="84" ry="100" fill="var(--berry)" stroke="var(--ink)" stroke-width="6" role="img" aria-label="Strawberry illustration with green leaves"/>
      <polygon class="star" points="88,582 93,594 106,594 96,602 100,615 88,607 76,615 80,602 70,594 83,594" fill="var(--ink)"/>
      <polygon class="star" points="290,582 295,594 308,594 298,602 302,615 290,607 278,615 282,602 272,594 285,594" fill="var(--ink)"/>
      <g class="rules" stroke="var(--ink)" stroke-width="3">
        <line x1="122" y1="627" x2="252" y2="627"/>
        <line x1="43" y1="640" x2="331" y2="640"/>
        <line x1="43" y1="708" x2="331" y2="708"/>
        <line x1="122" y1="721" x2="252" y2="721"/>
      </g>
    </svg>
    <h2 class="brand">
      <span class="brand__line brand__line--top">MEADOW</span>
      <span class="brand__line brand__line--mid">HUSH</span>
      <span class="brand__line brand__line--bottom">NATURALS</span>
    </h2>
    <p class="flavour">STRAWBERRY</p>
    <p class="product product--wide">SHAMPOO+BODY<br>WASH</p>
    <p class="size-mark">T</p>
  </section>
</main>
</body>
</html>
```